Skiing Company Needs A5 28page Skiing Catalogue

ABOUT THE BUSINESS/COMPANY:
- We are a guided skiing company called "Silver Lantern Journeys" and "Kestrel Ridge Alpine Society".

ABOUT THE CATALOGUE:

- We need an A5 28 page catalogue. ALL THE FILES (like photos and logos) are in the zip folders.

- You can look at the 000 KRS Catalog Word Document. Instructions on what text and photos to use are labeled there per Page.

Target Market(s)

Advanced/ Expert Skiers and Snowboarders that are thinking of joining a tour

Industry/Entity Type

Travel Agent

Font styles to use
Serif

Colors
ffffff
ec1f27
0455a3

Requirements
Must have
• NEED a 3mm bleed
• This is included on the 000 KRS Catalog word document
Nice to have
• Our main color is dark blue (just like our logo). Some red is ok but the main focus should be the dark blue.
Should not have
• Words/ Letters in the color red

```html
<!DOCTYPE html>
<html lang="en">
<head>
<meta charset="utf-8">
<title>About Us – Catalogue Spread</title>
<link rel="stylesheet" href="https://fonts.googleapis.com/css2?family=Merriweather:wght@300;400;700&family=Montserrat:wght@700&display=swap">
<style>
  :root {
    --paper: #ffffff;
    --brand-blue: #0455a3;
    --ink: #2b2b2b;
    --backdrop: #e9e6e1;
    --sky-top: #1d5fb0;
    --sky-low: #8fb8e2;
    --snow: #eef3f8;
    --snow-shade: #c9d6e4;
  }
  * { box-sizing: border-box; margin: 0; padding: 0; }
  html, body {
    width: 1200px; height: 1200px; overflow: hidden;
    background: var(--backdrop);
  }
  .spread {
    position: absolute; left: 20px; top: 190px;
    width: 1160px; height: 819px;
    background: var(--paper);
    box-shadow: 0 6px 18px rgba(0,0,0,0.18);
    overflow: hidden;
  }
  .spread-fold {
    position: absolute; top: 0; left: 556px; width: 48px; height: 100%;
    background: linear-gradient(90deg, rgba(0,0,0,0) 0%, rgba(0,0,0,0.06) 48%, rgba(0,0,0,0.12) 50%, rgba(0,0,0,0.03) 56%, rgba(0,0,0,0) 100%);
    pointer-events: none;
  }
  .photo { position: absolute; top: 0; height: 469px; }
  .photo-heli {
    left: 0; width: 866px;
    background: linear-gradient(180deg, var(--sky-top) 0%, var(--sky-low) 50%, var(--snow) 56%, var(--snow-shade) 100%);
  }
  .photo-sled {
    left: 873px; width: 287px;
    background: linear-gradient(180deg, #3d6fae 0%, #9bb6d2 26%, #c8d2dc 45%, #8f9aa6 62%, var(--snow) 78%, #dfe7f0 100%);
  }
  .copy {
    position: absolute; top: 494px;
    width: 232px;
    font-family: "Merriweather", Georgia, serif;
    font-weight: 300;
    font-size: 12.4px;
    line-height: 16.7px;
    color: var(--ink);
    text-align: justify;
  }
  .col-1 { left: 46px; }
  .col-2 { left: 302px; }
  .col-3 { left: 626px; }
  .col-4 { left: 882px; }
  .copy p + p, .copy p + ol { margin-top: 16.7px; }
  .copy strong { font-weight: 700; }
  .section-title {
    font-family: "Montserrat", Arial, sans-serif;
    font-weight: 700;
    font-size: 33px;
    line-height: 34px;
    color: var(--brand-blue);
    letter-spacing: 0.5px;
    margin: 0 0 18px 0;
    text-align: left;
  }
  .constants {
    list-style: none;
    font-weight: 700;
  }
  .constants li {
    padding-left: 20px; text-indent: -20px;
  }
</style>
</head>
<body>
  <main class="spread">
    <div class="photo photo-heli" role="img" aria-label="Photo: heli-ski group unloading gear in the snow beside a landed helicopter under a clear blue sky"></div>
    <div class="photo photo-sled" role="img" aria-label="Photo: rider on a snowmobile spraying powder above snowy forested mountains"></div>

    <section class="copy col-1">
      <h1 class="section-title">ABOUT US</h1>
      <p>Welcome to our <strong>14th season</strong> of Silver Lantern Lodge, Silver Lantern Journeys and Northwind Auto. The 2018 season also marks our 5th season of the Kestrel Ridge Alpine Society, our mechanized wing of KTR Trading.</p>
      <p>KTR (which stands for Kita Trail Roads) was established in Oct of 2003 when our founder Rowan Ashcombe went "all in" and decided to purchase a lodge in</p>
    </section>

    <section class="copy col-2">
      <p>Higashiyama to serve as a base to finally pursue his dream of starting a tour company dedicated to hardcore skiers and boarders while also offering a low cost rental car alternative allowing expat families and friends the ability explore the wonders of Hokkaido on their own.</p>
      <p>A lot has transpired in the past 14 years. Tours grew from just a single guide to a world class team of over 16 guides with experience and training from around the world, our vehicle rental program</p>
    </section>

    <section class="copy col-3">
      <p>has grown to include everything from budget to baller, our lodge has seen a plethora of upgrades and KRS was born and now offers Japan's best snowmobile, heli and cat tours.</p>
      <p>While change is inevitable, two things remain constant for us:</p>
      <ol class="constants">
        <li>1. Our love of sharing Hokkaido's incredible natural assets with you, our valued guests</li>
        <li>2. Our passion to help make Hokkaido a world class adventure sports destination.</li>
      </ol>
    </section>

    <section class="copy col-4">
      <p>Becoming world class can only be accomplished by hard work, determination, education and cooperation. The road has been very difficult at times but as we all know, few things in life worth doing come easy. With your continued support and feedback, Hokkaido WILL get there!</p>
    </section>

    <div class="spread-fold" aria-hidden="true"></div>
  </main>
</body>
</html>
```